Family business needs stationery redesign with new logo

Family owned company, established in 1987 wanting a brand 'refresh'. We are an electrical, refrigeration and construction company based in the Barkly Region Northern Territory, Australia. We have a new logo we would like to use which is uploaded along with our current letterhead and email signature. We are also dropping the word 'contractors' so please do not include this on any designs. Please note also, the 'orange' color used in our logo and designs should be Northern Territory red ochre which is as follows:

RGB (Hex): #C75B12
PantoneĀ® 159 C
CMYK: 1 / 74 / 100 / 7

We are needing our stationery redesigned using our new logo. Please include letterheads, business cards, envelopes, and email signatures.

We currently use our business letterheads for quotations, invoices, letters, HR matters, and internal memos.

We also need a separate simplified letterhead for internal paperwork such as employee leave forms, meeting agendas, and meeting minutes etc.

Reason: Needing more submissions of full package designs. We are wanting all our stationery, including business cards, letterheads, email signatures, envelopes, etc to be cohesive. We also require ALL the information, as supplied on our template letterhead, to be included on the new letterhead designs. including electrical license no.etc Thank you, R&W

Reason: needing more time as work has got in the way of looking over designs. A lot of designs not meeting the brief/criteria.

Industry/Entity Type

Business

Colors
0355a3
f37122

Requirements
Must have
• The 'orange' color used in the designs should be Northern Territory red ochre which is as follows:
• RGB (Hex): #C75B12
• PantoneĀ® 159 C
• CMYK: 1 / 74 / 100 / 7
• ***MUST INCLUDE ALL INFORMATION THAT IS ON OUR CURRENT LETTERHEAD***
Should not have
• Please do not include the word 'contractors'

```html
<!DOCTYPE html>
<html lang="en">
<head>
<meta charset="utf-8">
<title>R&amp;W Stationery</title>
<link rel="stylesheet" href="https://fonts.googleapis.com/css2?family=Arimo:wght@400;700&family=PT+Sans:wght@400;700&display=swap">
<style>
:root{
  --navy:#1b3170;
  --ochre:#c75b12;
  --paper:#ffffff;
  --bg:#e4e4e4;
  --ink:#222222;
  --muted:#555555;
  --fold:#d8d8d8;
}
*{margin:0;padding:0;box-sizing:border-box}
html,body{width:1200px;height:715px;overflow:hidden;background:var(--bg)}
.canvas{position:relative;width:1200px;height:715px}
.piece{position:absolute;background:var(--paper);box-shadow:0 2px 4px rgba(0,0,0,.18)}
.piece svg.art{position:absolute;left:0;top:0}
.wordmark{position:absolute;font-family:"PT Sans",sans-serif;font-weight:700;line-height:1;transform:translate(-50%,-50%);white-space:nowrap}
.wordmark--navy{color:var(--navy)}
.wordmark--white{color:#fff}

/* letterhead */
.letterhead{left:188px;top:67px;width:440px;height:620px;font-family:"PT Sans",sans-serif}
.letterhead .tagline{position:absolute;top:164px;left:0;width:100%;text-align:center;font-size:10px;color:var(--navy)}
.letterhead .body{position:absolute;left:33px;top:223px;width:385px;font-size:7.4px;line-height:9.6px;color:var(--ink)}
.letterhead .body p{margin-bottom:9.6px}
.letterhead .signoff{position:absolute;left:33px;top:405px;font-size:7.6px;color:var(--ink)}
.letterhead .footer{position:absolute;left:0;top:584px;width:100%;text-align:center;font-size:7.6px;line-height:10.8px;color:#fff}
.label{color:var(--ochre)}

/* business cards */
.card{width:240px;height:138px;border-radius:7px;overflow:hidden;font-family:Arimo,sans-serif}
.card--front{left:48px;top:160px}
.card--back{background:var(--ochre)}
.card--back-a{left:48px;top:325px}
.card--back-b{left:48px;top:482px}
.card--wide{left:748px;top:43px;width:284px;height:138px;border-radius:0}
.card .details{position:absolute;color:#fff}
.card .name{color:var(--ochre);font-weight:700;text-transform:uppercase}
.card .contact{list-style:none}
.card .contact li{display:flex;align-items:center}
.card .contact svg{margin-right:4px;flex:none}
.card--front .details{left:11px;top:31px;font-size:5.6px;line-height:7px}
.card--front .name{font-size:8px;line-height:9px}
.card--front .role{font-size:6px;margin-bottom:7px}
.card--front .address{margin-bottom:6px}
.card--front .contact li{height:9px}
.card--wide .details{left:14px;top:19px;font-size:8px;line-height:9.6px}
.card--wide .name{font-size:11.5px;line-height:13px}
.card--wide .role{font-size:8px;margin-bottom:9px}
.card--wide .address{margin-bottom:7px}
.card--wide .contact li{height:11.5px}
.card--back .est{position:absolute;left:0;width:100%;bottom:14px;text-align:center;font-family:"PT Sans",sans-serif;font-size:9.6px;color:#fff;letter-spacing:.3px}

/* envelopes */
.envelope{width:517px;height:232px;font-family:"PT Sans",sans-serif}
.envelope--back{left:642px;top:210px}
.envelope--front{left:642px;top:456px}
.envelope .return-address{position:absolute;left:25px;top:83px;font-size:8px;line-height:11px;color:var(--muted)}
</style>
</head>
<body>
<div class="canvas">

  <!-- Letterhead -->
  <section class="piece letterhead" aria-label="Letterhead">
    <svg class="art" width="440" height="620" viewBox="0 0 440 620" aria-hidden="true">
      <path d="M0 560 Q220 590 440 556 L440 620 L0 620 Z" fill="var(--navy)"/>
      <path d="M0 556 Q220 586 440 552" fill="none" stroke="var(--ochre)" stroke-width="2"/>
    </svg>
    <span class="wordmark wordmark--navy" style="left:220px;top:64px;font-size:42px">R&amp;W</span>
    <p class="tagline">Electrical - Refrigeration - Building Services</p>
    <div class="body">
      <p>Lorem ipsum dolor sit amet, consectetur adipiscing elit. Donec orci purus, luctus vitae dignissim eu, iaculis sed purus. Vivamus faucibus, ipsum nec aliquet viverra, leo mauris condimentum ligula, sit amet sagittis enim ligula quis arcu. Nam egestas tortor id nisi porttitor mattis. In tortor ante, ultricies in suscipit a, tempus non massa. Vivamus et auctor mi.</p>
      <p>Aliquam erat volutpat. Nulla facilisi. Integer porta diam eget urna vulputate semper a. Phasellus nec eros mauris, et scelerisque orci. Donec malesuada orci vitae nulla accumsan luctus. Quisque accumsan iaculis magna sit amet fringilla. Maecenas consequat, magna eget tincidunt rutrum mi, id feugiat ante nisi eu risus. Vestibulum nunc orci, rhoncus a placerat in, ultricies varius eros, vel fringilla nisi suscipit eget.</p>
      <p>Curabitur vel sagittis nulla at porttitor. Mauris a justo et tellus interdum tristique. Sed id augue vitae urna aliquet a quam. Pellentesque arcu velit, cursus et malesuada ut, consequat et diam. Nullam ullamcorper vitae, rhoncus et arcu. In ultricies ultricies nulla, ut rutrum nisi iaculis at. Donec ornare faucibus.</p>
      <p>Nam tempus ultricies. Morbi semper, est id tincidunt gravida, sem arcu adipiscing lacus, ac bibendum dolor. Quisque nec diam sed risus consectetur a ccumsan quis quis nibh. Vestibulum id purus lorem.</p>
    </div>
    <p class="signoff">Jane Hart</p>
    <div class="footer">
      <p>64 Dalton St, PO Box, Warrego NT. 0862</p>
      <p>ABN 47 219 803 | Refrigerant Trading Authorisation 603918 | NT Electrical License 41257</p>
      <p><span class="label">P :</span> 08 8951 2043 <span class="label">F :</span> 08 8951 2044 <span class="label">E :</span> info@rwservices.com.au <span class="label">W :</span> rwservices.com.au</p>
    </div>
  </section>

  <!-- Business card front -->
  <section class="piece card card--front" aria-label="Business card front">
    <svg class="art" width="240" height="138" viewBox="0 0 240 138" aria-hidden="true">
      <rect width="240" height="138" fill="var(--navy)"/>
      <path d="M200 0 C130 5 95 55 104 80 C112 112 150 132 180 138" fill="none" stroke="var(--ochre)" stroke-width="5"/>
      <path d="M204 0 C136 6 100 56 109 80 C117 111 155 131 185 138 L240 138 L240 0 Z" fill="#fff"/>
    </svg>
    <span class="wordmark wordmark--navy" style="left:174px;top:73px;font-size:30px">R&amp;W</span>
    <div class="details">
      <p class="name">Alan Brooks</p>
      <p class="role">CEO/Founder</p>
      <p class="address">4120 Maple Court<br>Juneau, Alaska 34512</p>
      <ul class="contact">
        <li><svg width="6" height="6" viewBox="0 0 10 10"><path d="M2 0 L4 3 L3 4 Q4 6 6 7 L7 6 L10 8 L8 10 Q2 9 0 2 Z" fill="var(--ochre)"/></svg>612 904 3371</li>
        <li><svg width="6" height="6" viewBox="0 0 10 10"><rect x="2" y="0" width="6" height="3" fill="var(--ochre)"/><rect x="0" y="4" width="10" height="4" fill="var(--ochre)"/><rect x="2" y="8" width="6" height="2" fill="var(--ochre)"/></svg>455 217 8806</li>
        <li><svg width="6" height="6" viewBox="0 0 10 10"><rect x="0" y="2" width="10" height="7" fill="var(--ochre)"/><path d="M0 2 L5 6 L10 2" fill="none" stroke="var(--navy)" stroke-width="1"/></svg>mail@sitename.com</li>
        <li><svg width="6" height="6" viewBox="0 0 10 10"><circle cx="5" cy="5" r="5" fill="var(--ochre)"/><path d="M5 0 V10 M0 5 H10" stroke="var(--navy)" stroke-width="0.8"/></svg>www.sitename.com</li>
      </ul>
    </div>
  </section>

  <!-- Business card backs -->
  <section class="piece card card--back card--back-a" aria-label="Business card back">
    <span class="wordmark wordmark--white" style="left:120px;top:67px;font-size:40px">R&amp;W</span>
    <p class="est">Est. 1987</p>
  </section>
  <section class="piece card card--back card--back-b" aria-label="Business card back">
    <span class="wordmark wordmark--white" style="left:120px;top:67px;font-size:40px">R&amp;W</span>
    <p class="est">Est. 1987</p>
  </section>

  <!-- Wide business card -->
  <section class="piece card card--wide" aria-label="Business card">
    <svg class="art" width="284" height="138" viewBox="0 0 284 138" aria-hidden="true">
      <rect width="284" height="138" fill="var(--navy)"/>
      <path d="M188 0 C140 15 125 50 133 78 C140 110 175 130 208 138" fill="none" stroke="var(--ochre)" stroke-width="5"/>
      <path d="M193 0 C146 16 131 50 138 78 C145 109 180 129 213 138 L284 138 L284 0 Z" fill="#fff"/>
    </svg>
    <span class="wordmark wordmark--navy" style="left:214px;top:69px;font-size:36px">R&amp;W</span>
    <div class="details">
      <p class="name">Alan Brooks</p>
      <p class="role">CEO/Founder</p>
      <p class="address">4120 Maple Court<br>Juneau, Alaska 34512</p>
      <ul class="contact">
        <li><svg width="8" height="8" viewBox="0 0 10 10"><path d="M2 0 L4 3 L3 4 Q4 6 6 7 L7 6 L10 8 L8 10 Q2 9 0 2 Z" fill="var(--ochre)"/></svg>612 904 3371</li>
        <li><svg width="8" height="8" viewBox="0 0 10 10"><rect x="2" y="0" width="6" height="3" fill="var(--ochre)"/><rect x="0" y="4" width="10" height="4" fill="var(--ochre)"/><rect x="2" y="8" width="6" height="2" fill="var(--ochre)"/></svg>455 217 8806</li>
        <li><svg width="8" height="8" viewBox="0 0 10 10"><rect x="0" y="2" width="10" height="7" fill="var(--ochre)"/><path d="M0 2 L5 6 L10 2" fill="none" stroke="var(--navy)" stroke-width="1"/></svg>mail@sitename.com</li>
        <li><svg width="8" height="8" viewBox="0 0 10 10"><circle cx="5" cy="5" r="5" fill="var(--ochre)"/><path d="M5 0 V10 M0 5 H10" stroke="var(--navy)" stroke-width="0.8"/></svg>www.sitename.com</li>
      </ul>
    </div>
  </section>

  <!-- Envelope back -->
  <section class="piece envelope envelope--back" aria-label="Envelope back">
    <svg class="art" width="517" height="232" viewBox="0 0 517 232" aria-hidden="true">
      <path d="M0 232 L205 86 M517 232 L312 86" stroke="var(--fold)" stroke-width="1" fill="none"/>
      <path d="M0 0 L517 0 L511 62 Q506 86 484 86 L35 86 Q14 86 9 64 Z" fill="var(--ochre)"/>
    </svg>
    <span class="wordmark wordmark--white" style="left:258px;top:44px;font-size:32px">R&amp;W</span>
  </section>

  <!-- Envelope front -->
  <section class="piece envelope envelope--front" aria-label="Envelope front">
    <svg class="art" width="517" height="232" viewBox="0 0 517 232" aria-hidden="true">
      <path d="M0 200 Q258 226 517 200 L517 232 L0 232 Z" fill="var(--navy)"/>
      <path d="M0 195 Q258 221 517 195" fill="none" stroke="var(--ochre)" stroke-width="2"/>
    </svg>
    <span class="wordmark wordmark--navy" style="left:77px;top:48px;font-size:36px">R&amp;W</span>
    <p class="return-address">64 Dalton St, PO Box<br>Warrego NT. 0862</p>
  </section>

</div>
</body>
</html>
```